business card - for laser marking

I need design (curve) for my business card (make with laser) size 85mm x 55mm. How it look business card with laser marking see attached picture.

color:
Background: white
text and icons black

Please include: one side
1. dominik vrabec - direktor
2. phone: +386(0)41 726 190
+386(0)580 237 61
3. info@zarezko.example
4. faecebook.com/Zarezko.Ex
5. KM-ATELJE, Dominik Vrabec s.p.
Lipova ulica 19, 1000 Ljubljana, SI
6. logo

Please include: second side
1. logo
2. www.zarezko.example
3. Lasersko graviranje
ovitki telefonov, ohišja telefonov / tablic, nakit, ure, alu vizitke, dog-tagi, kemični svinčniki, orodja, noži, vžigalniki

Industry/Entity Type

Business

Contact Information for Business Card

Please include: one side
+386(0)580 237 61
3. info@zarezko.example
6. logo

1. logo
2. www.zarezko.example
3. Lasersko graviranje

Colors
000000
ffffff

Requirements
Must have
• I need design (curve) for my business card (make with laser) size 85mm x 55mm. How it look business card with laser marking see attached picture.
• color:
• Background: white
• text and icons black
• Please include: one side
• 1. dominik vrabec - direktor
• 2. phone: +386(0)41 726 190
• +386(0)580 237 61
• 3. info@zarezko.example
• 4. faecebook.com/Zarezko.Ex
• 5. KM-ATELJE, Dominik Vrabec s.p.
• Lipova ulica 19, 1000 Ljubljana, SI
• 6. logo
• Please include: second side
• 1. logo
• 2. www.zarezko.example
• 3. Lasersko graviranje
• ovitki telefonov, ohišja telefonov / tablic, nakit, ure, alu vizitke, dog-tagi, kemični svinčniki, orodja, noži, vžigalniki

```html
<!DOCTYPE html>
<html lang="sl">
<head>
<meta charset="utf-8">
<title>Zarezko – vizitka</title>
<link rel="stylesheet" href="https://fonts.googleapis.com/css2?family=Roboto:wght@400;500;700&family=Roboto+Condensed:wght@400;700&display=swap">
<style>
  :root {
    --bg: #e9e6e1;
    --card-white: #f4f4f4;
    --green: #62a337;
    --pink: #d6144f;
    --ink: #3a3a3a;
    --muted: #7a7a7a;
    --rule: #c9c9c9;
    --card-dark: #1e1f21;
    --on-dark: #f2f2f2;
  }
  * { box-sizing: border-box; margin: 0; padding: 0; }
  html, body { width: 1200px; height: 911px; overflow: hidden; }
  body {
    background: var(--bg);
    font-family: "Roboto", Arial, sans-serif;
    position: relative;
  }
  .card {
    position: absolute;
    width: 520px;
    height: 336px;
    border-radius: 18px;
    overflow: hidden;
    box-shadow: 0 10px 26px rgba(0,0,0,.22);
  }
  .card--front { left: 60px; top: 70px; background: var(--card-white); }
  .card--back  { left: 620px; top: 505px; background: var(--card-dark); color: var(--on-dark); }

  .front-waves { position: absolute; inset: 0; }

  .holder { position: absolute; right: 28px; top: 22px; text-align: right; }
  .holder__name {
    font-family: "Roboto Condensed", Arial, sans-serif;
    font-weight: 700; font-size: 26px; color: var(--pink);
    text-transform: uppercase; letter-spacing: .3px;
  }
  .holder__role {
    font-family: "Roboto Condensed", Arial, sans-serif;
    font-size: 14px; color: var(--muted); text-transform: uppercase; margin-top: 2px;
  }

  .brand {
    position: absolute; left: 34px; bottom: 40px;
    display: flex; align-items: center; gap: 10px;
  }
  .brand__dot { width: 22px; height: 22px; border-radius: 50%; background: var(--green); }
  .brand__name { font-weight: 700; font-size: 38px; color: var(--pink); letter-spacing: .5px; }

  .contact {
    position: absolute; left: 290px; top: 128px; width: 210px;
    font-size: 13px; color: var(--ink); line-height: 1.45;
  }
  .contact__company { padding-bottom: 10px; border-bottom: 1px solid var(--rule); margin-bottom: 10px; }
  .contact__line { display: flex; align-items: center; gap: 8px; }
  .contact__line svg { width: 12px; height: 12px; flex: none; }

  .back-brand {
    position: absolute; left: 40px; top: 44px;
    display: flex; align-items: center; gap: 10px;
  }
  .back-brand__dot { width: 20px; height: 20px; border-radius: 50%; background: var(--green); }
  .back-brand__name { font-weight: 700; font-size: 34px; color: var(--on-dark); }
  .services {
    position: absolute; left: 40px; right: 40px; top: 130px;
    text-align: center; font-size: 15px; line-height: 1.5;
  }
  .services__title { font-weight: 500; font-size: 17px; margin-bottom: 4px; }
  .services__url { color: var(--pink); font-weight: 700; font-size: 17px; margin-top: 14px; }
</style>
</head>
<body>
  <section class="card card--front" aria-label="Sprednja stran vizitke">
    <svg class="front-waves" viewBox="0 0 520 336" aria-hidden="true">
      <path d="M0 0 H230 C190 40 170 120 90 170 C50 195 20 215 0 240 Z" fill="var(--green)"/>
      <path d="M230 0 H258 C215 50 190 135 105 185 C60 210 25 232 0 262 V240 C20 215 50 195 90 170 C170 120 190 40 230 0 Z" fill="var(--pink)"/>
      <path d="M0 290 C40 240 110 215 175 205 C110 225 50 255 10 300 Z" fill="var(--green)"/>
    </svg>

    <header class="holder">
      <h1 class="holder__name">Dominik Vrabec</h1>
      <p class="holder__role">Direktor</p>
    </header>

    <div class="brand">
      <span class="brand__dot"></span>
      <span class="brand__name">Zarezko</span>
    </div>

    <div class="contact">
      <div class="contact__company">
        KM-ATELJE<br>
        Dominik Vrabec s.p.<br>
        Lipova ulica 19<br>
        1000 Ljubljana, SI
      </div>
      <div class="contact__line">
        <svg viewBox="0 0 12 12"><path d="M2 1h2.5l1 2.5-1.4 1a6 6 0 0 0 3.4 3.4l1-1.4L11 7.5V10a1 1 0 0 1-1 1A9 9 0 0 1 1 2a1 1 0 0 1 1-1z" fill="var(--pink)"/></svg>
        +386(0)580 237 61
      </div>
      <div class="contact__line">
        <svg viewBox="0 0 12 12"><rect x="3" y="0.5" width="6" height="11" rx="1.2" fill="none" stroke="var(--pink)" stroke-width="1.3"/><circle cx="6" cy="9.5" r=".8" fill="var(--pink)"/></svg>
        +386(0)41 726 190
      </div>
      <div class="contact__line">
        <svg viewBox="0 0 12 12"><rect x="0.5" y="2" width="11" height="8" rx="1" fill="var(--pink)"/><path d="M1 2.5l5 4 5-4" fill="none" stroke="#fff" stroke-width="1"/></svg>
        info@zarezko.example
      </div>
      <div class="contact__line">
        <svg viewBox="0 0 12 12"><rect x="0.5" y="0.5" width="11" height="11" rx="1.5" fill="var(--pink)"/></svg>
        faecebook.com/Zarezko.Ex
      </div>
    </div>
  </section>

  <section class="card card--back" aria-label="Zadnja stran vizitke">
    <div class="back-brand">
      <span class="back-brand__dot"></span>
      <span class="back-brand__name">Zarezko</span>
    </div>
    <div class="services">
      <p class="services__title">Lasersko graviranje</p>
      <p>ovitki telefonov, ohišja telefonov / tablic, nakit, ure, alu vizitke<br>
      dog-tagi, kemični svinčniki, orodja, noži, vžigalniki</p>
      <p class="services__url">www.zarezko.example</p>
    </div>
  </section>
</body>
</html>
```